Flyer für Verkauf von Radondetektoren
Zielgruppe
Ich verkaufe Radondetektoren zur Messung von Radon in Innenräumen. Zielgruppe sind Privatpersonen, Firmen, Genossenschaften und andere Hauseigentümer.
Aufgabenstellung
Ich brauche das Design für meine Messanleitung.
Kreativ - modern - weniger kann mehr sein
Struktur ist wichtigt, es soll also einfach sein zu lesen und zu verstehen, was gemacht werden soll. Können Bulletpoints, Icons mit eingebracht werden.
Wichtig ist auch, dass die beiden Logos 'Luftprüfer.de' und TESTOVAL' auf der Messanleitung vorhanden sind. Wobei 'Luftprüfer.de' das Hauptlogo ist.
DIN format dachte ich A4 beidseitig (Text müsste also auf diese Grösse angepasst werden).
Kann natürlich auch Flyer-Format sein oder andere Vorschläge!
Bildmaterial gibt es auf unsere Homepage https://luftprüfer.de und https://luftkontroll.se . Diese haben wir bereits gekauft und können verwendet werden. Ich lade sie den bei Bedarf hoch. Es können natürlich auch andere Vorschläge kommen.

```html
<!DOCTYPE html>
<html lang="de">
<head>
<meta charset="utf-8">
<title>Messanleitung – Luftprüfer.de</title>
<link href="https://fonts.googleapis.com/css2?family=Montserrat:wght@500;600&family=Open+Sans:ital,wght@0,400;0,600;0,700;1,400&display=swap" rel="stylesheet">
<style>
  :root{
    --red:#c8282e;
    --ink:#2b2b2b;
    --text:#3d3d3d;
    --page:#f3f3f3;
    --band:#e4e4e6;
    --canvas:#ececec;
    --partner:#3e4c9c;
  }
  *{box-sizing:border-box;margin:0;padding:0}
  html,body{width:1200px;height:800px;overflow:hidden;background:var(--canvas)}
  body{font-family:"Open Sans",Arial,sans-serif;color:var(--text);position:relative}
  .sheet{position:absolute;top:18px;width:540px;height:764px;background:var(--page);overflow:hidden;display:flex;flex-direction:column;box-shadow:0 2px 10px rgba(0,0,0,.12)}
  .sheet--front{left:40px}
  .sheet--back{left:620px}
  p,li{font-size:6.6px;line-height:1.65}
  .accent{color:var(--red)}
  strong.accent{font-weight:700}

  .masthead{background:var(--red);color:#fff;text-align:center;padding:24px 20px 18px}
  .masthead__title{font-family:"Montserrat",Arial,sans-serif;font-weight:600;font-size:27px;letter-spacing:.5px;line-height:1}
  .masthead__sub{font-family:"Montserrat",Arial,sans-serif;font-weight:600;font-size:9.6px;margin-top:9px}

  .step{padding:16px 26px 4px}
  .step__head{display:flex;align-items:center;gap:7px;margin-bottom:9px}
  .step__badge{width:22px;height:22px;flex:none;border:1.6px solid var(--red);border-radius:50%;color:var(--red);font-family:"Montserrat",Arial,sans-serif;font-weight:600;font-size:11px;display:flex;align-items:center;justify-content:center}
  .step__num{font-family:"Montserrat",Arial,sans-serif;color:var(--red);font-weight:600;font-size:10.5px;line-height:1.1}
  .step__name{font-weight:700;font-size:7.6px;color:var(--ink);text-transform:uppercase}
  .step p+p{margin-top:6px}
  .note{font-style:italic}

  .rooms{background:var(--band);margin-top:12px;flex:1;display:flex;padding:16px 26px 0;gap:24px}
  .rooms__col{flex:1;display:flex;flex-direction:column}
  .section-title{font-weight:600;font-size:13.5px;color:var(--ink);border-left:2.5px solid var(--red);padding-left:6px;line-height:1;margin-bottom:16px}
  .subhead{display:flex;justify-content:space-between;align-items:center;color:var(--red);font-weight:700;font-size:8px;line-height:1.4;margin-bottom:7px}
  .subhead svg{width:24px;height:24px;flex:none}
  .bullets{list-style:none;margin-bottom:12px}
  .bullets li{position:relative;padding-left:15px;margin-bottom:4px}
  .bullets li::before{content:"";position:absolute;left:1px;top:3px;width:6px;height:6px;border-radius:50%;background:var(--red)}

  .brand{margin-top:auto;margin-bottom:18px}
  .brand__name{font-size:22px;color:var(--ink);font-weight:400;line-height:1}
  .partner{display:flex;align-items:center;justify-content:center;gap:7px;margin-top:8px}
  .partner__mark{width:13px;height:13px;background:var(--partner)}
  .partner__name{font-size:22px;color:var(--partner);font-weight:400;line-height:1}
  .scene{margin:10px -26px 0 -14px;flex:1;min-height:120px;background:linear-gradient(180deg,#e4e4e6 0%,#c7d7ea 30%,#8d7fc0 55%,#6aa24a 80%,#5a9b3c 100%);border-radius:60px 0 0 0}
  .footer-strip{height:7px;background:var(--red)}

  .placement{background:var(--band);padding:22px 26px 14px}
  .placement .section-title{margin-bottom:14px}
  .placement .bullets li{margin-bottom:6px}
  .split{display:flex;gap:22px}
  .split>*{flex:1;min-width:0}
  .split h4{color:var(--red);font-size:8.4px;font-weight:700;margin-bottom:7px}
  .address{display:flex;align-items:center;gap:12px;margin:12px 0 10px}
  .address svg{width:26px;height:20px;flex:none}
  .address p{font-size:7.4px;font-weight:700;color:var(--red);line-height:1.7}
  .hints{background:var(--red);margin:14px 18px 0;padding:6px}
  .hints__frame{border:1.5px solid #fff;padding:10px 14px 4px;color:#fff}
  .hints h4{font-size:8.8px;font-weight:600;margin-bottom:7px}
  .hints .bullets{margin-bottom:6px}
  .hints .bullets li{color:#fff;margin-bottom:6px}
  .hints .bullets li::before{background:#fff}
  .legal{margin-top:auto;background:var(--red);color:#fff;text-align:center;font-weight:600;font-size:7.6px;padding:10px 0 14px}
</style>
</head>
<body>

<article class="sheet sheet--front">
  <header class="masthead">
    <h1 class="masthead__title">MESSANLEITUNG</h1>
    <p class="masthead__sub">FÜR RADONMESSUNGEN VON INNENRAUMLUFT MIT PASSIVEN RADON DETEKTOREN</p>
  </header>

  <section class="step">
    <div class="step__head">
      <span class="step__badge">1</span>
      <div><div class="step__num">SCHRITT 1:</div><div class="step__name">Registrierung und Anmeldung</div></div>
    </div>
    <p>Wenn Sie Neukunde sind, legen Sie bitte zunächst ein neues Benutzerkonto auf unserem Online-Portal <strong class="accent">https://kundenportal.testoval.se/de an.</strong> Anschließend können Sie die Radondetektoren registrieren. Vermerken Sie den Start der Messung (Datum und Uhrzeit), die Messorte (Raum und Etage) sowie die 9-stellige Seriennummer der Detektoren, die Sie auf der Verpackung oder auf der Unterseite der jeweiligen Detektoren finden.</p>
    <p class="note">Firmenkunden haben die Möglichkeit eine Excel-Datei als Hilfsmittel herunterzuladen, die Sie ausfüllen und dann wieder hochladen.</p>
  </section>

  <section class="step">
    <div class="step__head">
      <span class="step__badge">2</span>
      <div><div class="step__num">SCHRITT 2:</div><div class="step__name">Platzierung der Detektoren</div></div>
    </div>
    <p>Bevor Sie die Detektoren der Verpackung entnehmen, überlegen Sie wo genau Sie die Radondetektoren platzieren wollen. Die Radonmessung beginnt, sobald Sie die radondichten Verpackungen öffnen. Beachten Sie bei der Platzierung zunächst die <strong class="accent">Auswahl der Räume</strong> und <strong class="accent">die Positionierung der Radondetektoren im Raum.</strong><br>Für eine zuverlässige Radonmessung empfehlen wir wie folgt vorzugehen:</p>
  </section>

  <section class="rooms">
    <div class="rooms__col">
      <h2 class="section-title">Die Auswahl der Räume:</h2>
      <h3 class="subhead">Radonmessungen für Einfamilienhäuser:
        <svg viewBox="0 0 26 26" fill="none" stroke="#c8282e" stroke-width="1.3"><path d="M3 12 L13 4 L23 12"/><rect x="6" y="12" width="14" height="11"/><rect x="11" y="16" width="4" height="7"/><rect x="7.5" y="14" width="2.5" height="2.5"/><rect x="16" y="14" width="2.5" height="2.5"/></svg>
      </h3>
      <ul class="bullets">
        <li>Es sollten mindestens zwei Wohnräume und pro bewohnte Etage mindestens ein Wohnraum gemessen werden. Wählen Sie Räume aus, in denen Sie sich oft aufhalten (z.B. das Wohn- und Schlafzimmer). Vermeiden Sie aber Räume, in denen das Fenster mehrere Stunden am Tag oder in der Nacht geöffnet ist.</li>
        <li>Insofern Sie einen Keller haben, empfehlen wir alle Kellerräume zu messen, da hier meist das größte Risiko einer erhöhten Radonkonzentration erwartet wird.</li>
      </ul>
      <h3 class="subhead">Radonmessungen für Arbeitsplätze und<br>öffentliche Gebäude:
        <svg viewBox="0 0 26 26" fill="none" stroke="#c8282e" stroke-width="1.3"><path d="M3 9 L13 3 L23 9 Z"/><path d="M4 23 H22"/><path d="M6 10 V21 M10 10 V21 M16 10 V21 M20 10 V21"/></svg>
      </h3>
      <ul class="bullets">
        <li>Wählen Sie Räume, die regelmäßig mehr als vier Stunden pro Tag genutzt werden.</li>
        <li>Messen Sie alle unterirdischen Räumlichkeiten, da hier meist das größte Risiko einer erhöhten Radonkonzentration erwartet wird.</li>
        <li>Messen Sie alle Räume im Erdgeschoß. Für größere Räumlichkeiten empfehlen wir einen Detektor pro 200 m².</li>
        <li>In den oberen Etagen sollten Sie mit mindestens zwei Detektoren, sowie mindestens einem Detektor pro 200 m² messen.</li>
      </ul>
      <div class="brand"><span class="brand__name">Luftprüfer.de</span></div>
    </div>

    <div class="rooms__col">
      <h3 class="subhead">Radonmessungen für Mehrfamilienhäuser,<br>Wohnungen und Wohnkomplexen:
        <svg viewBox="0 0 26 26" fill="none" stroke="#c8282e" stroke-width="1.3"><rect x="5" y="2" width="16" height="22"/><path d="M5 8 H21 M5 14 H21 M5 19 H21"/><rect x="8" y="4" width="3" height="2"/><rect x="15" y="4" width="3" height="2"/><rect x="8" y="10" width="3" height="2"/><rect x="15" y="10" width="3" height="2"/></svg>
      </h3>
      <ul class="bullets">
        <li>Alle Wohnungen mit direktem Bodenkontakt sowie mindestens eine Wohnung pro Etage sollten gemessen werden. Wählen Sie dabei Wohnungen, die an Aufzügen oder Luftschächten liegen.</li>
        <li>In größeren Wohnkomplexen sollten insgesamt mindestens 20% aller Wohnungen in einem Gebäude gemessen werden.</li>
        <li>Es sollten mindestens zwei Wohnräume pro ausgewählte Wohnung gemessen werden. Wählen Sie Räume aus, in denen Sie sich oft aufhalten (z.B. das Wohn- und Schlafzimmer). Vermeiden Sie aber Räume, in denen das Fenster mehrere Stunden am Tag oder in der Nacht geöffnet ist.</li>
        <li>Selbst bei einer Einzimmerwohnung sollten Sie zwei Detektoren aufstellen.</li>
      </ul>
      <div class="partner">
        <span class="partner__mark"></span>
        <span class="partner__name">Testoval</span>
      </div>
      <div class="scene" role="img" aria-label="Illustration: Stadtsilhouette mit Hochhäusern, grünen Hügeln, Bäumen und Wohnhäusern"></div>
    </div>
  </section>
  <div class="footer-strip"></div>
</article>

<article class="sheet sheet--back">
  <section class="placement">
    <h2 class="section-title">Platzierung der Detektoren im Raum:</h2>
    <ul class="bullets">
      <li>Platzieren Sie die Detektoren in einem Mindestabstand von 20 cm zu Wänden, 50 cm zu Abluftsventilen, sowie 1,50 m zu Fenstern, Außentüren, Zuluftsventilen und Heizkörpern.</li>
      <li>Stellen Sie die Detektoren nicht auf dem Boden, an starken Wärmequellen oder Luftströmen auf. Vermeiden Sie auch Räume mit hoher Luftfeuchtigkeit, wie zum Beispiel das Badezimmer.</li>
      <li>Die Detektoren können entweder stehend (auf einem Tisch, im Regal oder einer Schrankwand) oder hängend mitten im Raum (z.B. von einer Lampe) platziert werden.</li>
      <li>Stellen Sie die Detektoren während der gesamten Messdauer nicht um.</li>
      <li>Versuchen Sie nicht das Gehäuse der Detektoren zu öffnen und platzieren Sie diese immer außer Reichweite von Kindern.</li>
    </ul>
  </section>

  <section class="step">
    <div class="step__head">
      <span class="step__badge">3</span>
      <div><div class="step__num">SCHRITT 3:</div><div class="step__name">Radonmessung</div></div>
    </div>
    <p>Die Radonmessung beginnt, sobald Sie die radondichten Verpackungen öffnen. <span class="accent">Bitte halten Sie die Messdauer wie folgt ein:</span></p>
    <div class="split" style="margin-top:8px">
      <div>
        <h4>Kurzzeitmessung:</h4>
        <ul class="bullets">
          <li>Mindestmessdauer 10 Tage (bis hin zu 30 Tagen).</li>
          <li>Führen Sie die Messung vorzugsweise in der Heizperiode (1. Oktober – 30. April) durch.</li>
          <li>Kurzzeitmessungen werden oft beim Kauf oder Verkauf von Immobilien genutzt, um ein mögliches Gefährdungspotential abschätzen zu können, oder wenn die Zeit nicht ausreicht, um eine Langzeitmessung durchzuführen.</li>
        </ul>
      </div>
      <div>
        <h4>Langzeitmessung:</h4>
        <ul class="bullets">
          <li>Mindestmessdauer 3 Monate während der Heizperiode (1. Oktober – 30. April).</li>
          <li>Um einen Jahresmittelwert der Radonkonzentration in Innenräumen ermitteln zu können, halten Sie die Messdauer von 12 Monaten ein.</li>
          <li>Falls Ihr Arbeitsplatz in einem Radon-Vorsorgegebiet liegt und somit der Messpflicht unterliegt, muss die Messdauer von 12 Monaten eingehalten werden.</li>
        </ul>
      </div>
    </div>
  </section>

  <section class="step" style="padding-top:4px">
    <div class="step__head">
      <span class="step__badge">4</span>
      <div><div class="step__num">SCHRITT 4:</div><div class="step__name">Abschluss der Radonmessung mit abschliessendem Prüfbericht</div></div>
    </div>
    <p>Nach Ablauf der Messdauer, loggen Sie sich auf <strong class="accent">https://kundenportal.testoval.se/de</strong> in Ihrem Account ein. Vermerken Sie hier das Ende der Messung und senden Sie anschließend alle Radondetektoren ausreichend frankiert in einem Umschlag oder einem Karton zeitnah an unsere Rücksendeadresse:</p>
    <div class="address">
      <svg viewBox="0 0 26 20" fill="none" stroke="#c8282e" stroke-width="1.6"><rect x="1" y="1" width="24" height="18"/><path d="M1 1 L13 11 L25 1 M1 19 L10 9 M25 19 L16 9"/></svg>
      <p>Luftprüfer.de<br>Lindenhofstraße 14 – 28195 Musterstadt – Deutschland</p>
    </div>
    <p>Sobald die Radondetektoren im Labor von Testoval eingetroffen sind, werden diese fachgerecht analysiert und die Ergebnisse der Radonmessung ausgewertet. Ein vollständiger Prüfbericht wird Ihnen innerhalb 36 Stunden nach Erhalt der Detektoren im Labor per E-Mail zugeschickt.</p>
  </section>

  <section class="hints">
    <div class="hints__frame">
      <h4>Weitere Hinweise:</h4>
      <div class="split">
        <ul class="bullets">
          <li>Bitte beachten Sie, dass die Radonmessung innerhalb von 15 Monaten nach Kaufdatum abgeschlossen sein muss.</li>
          <li>Versuchen Sie nicht das Gehäuse der Detektoren zu öffnen und platzieren Sie diese immer außer Reichweite von Kindern.</li>
          <li>Während der gesamten Messdauer dürfen die Detektoren nicht an einem anderen Ort umplatziert werden.</li>
        </ul>
        <ul class="bullets">
          <li>Durch die Anmeldung auf der Website <strong>https://kundenportal.testoval.se/de</strong> und die Eingabe der erforderlichen Daten bestätigt der/die Wohnungseigentümer*in/Messverantwortliche, dass er/sie die Messanleitung befolgt hat und die Detektoren gemäß den Anweisungen korrekt platziert wurden.</li>
        </ul>
      </div>
    </div>
  </section>

  <footer class="legal">Datenschutz (GDPR), Impressum und AGBs: Mehr Information dazu finden Sie unter www.luftprüfer.de</footer>
</article>

</body>
</html>
```